Signage Design Project

We need a logo and signage for the shopfront of a personal fitness training gym and coaching facility. We want the signage to cover the glass shopfront windows which consist of 4 glass windows with dimensions: 1 of 200cm x 180cm, 2 of 180cm x 135cm and 1 of 180cm x 180cm. The windows that are 200x 180 and 180x180 are the most visable/ important. We want the 200x180 to display the logo and our name which is "Ridgeline Fitness Centre" with further information of: Your personal training studio and boutique coaching gym Ph: 9471 2836.
For the window with 180 x 180cm measurement we want to list the services we provide which are:
Personal Training Sessions | Group Classes|Weight Loss |Toning & Sculpting|Bodybuilding I Cardio|Weights| Kettlebells| Boxing| Circuits I Team Building Programs| Boot Camp I Healthy Lifestyle & Wellness Coaching
The 2 windows 180x135cm are diagonal to the entry of the shop. We want them to be the same and plainer in design with the words: Ridgeline Fitness Centre
Personal Training Studio and Boutique Coaching Gym
The signage design also includes an acrylic window box that lights up which is to display the logo and Ridgeline Fitness Centre

```html
<!DOCTYPE html>
<html lang="en">
<head>
<meta charset="utf-8">
<title>Ridgeline Fitness Centre – Signage Options</title>
<link rel="stylesheet" href="https://fonts.googleapis.com/css2?family=Russo+One&family=Poppins:wght@600&display=swap">
<style>
  :root {
    --teal: #0099bb;
    --label-teal: #1a9cc0;
    --page: #f4f4f4;
    --white: #ffffff;
  }
  * { box-sizing: border-box; margin: 0; padding: 0; }
  html, body {
    width: 1200px;
    height: 900px;
    overflow: hidden;
    background: var(--page);
  }
  .sheet {
    position: relative;
    width: 1200px;
    height: 900px;
  }
  .sign {
    position: absolute;
    width: 562px;
    height: 189px;
    background: var(--teal);
    color: var(--white);
  }
  .sign--light {
    background: var(--page);
    border: 1px solid var(--label-teal);
    color: var(--teal);
  }
  .sign__mark {
    position: absolute;
    left: 48px;
    top: 44px;
    width: 92px;
    height: 92px;
    background: currentColor;
  }
  .sign__mark--round { border-radius: 50%; }
  .sign__name {
    position: absolute;
    left: 158px;
    top: 34px;
    font-family: "Russo One", sans-serif;
    font-weight: 400;
    line-height: 1;
    text-transform: uppercase;
  }
  .sign__name-main {
    display: block;
    font-size: 58px;
    letter-spacing: 2px;
  }
  .sign__name-sub {
    display: block;
    margin-top: 6px;
    font-size: 27px;
    letter-spacing: 3px;
    text-transform: none;
  }
  .sign__phone {
    position: absolute;
    left: 198px;
    top: 148px;
    font-family: "Poppins", sans-serif;
    font-weight: 600;
    font-size: 24px;
    letter-spacing: 1.5px;
    word-spacing: 6px;
    line-height: 1;
  }
  .option-label {
    position: absolute;
    width: 80px;
    text-align: center;
    font-family: "Poppins", sans-serif;
    font-weight: 600;
    font-size: 15px;
    color: var(--label-teal);
  }
</style>
</head>
<body>
<main class="sheet">

  <section class="sign" style="left:22px; top:90px; height:188px;">
    <span class="sign__mark"></span>
    <h1 class="sign__name"><span class="sign__name-main">Ridgeline</span><span class="sign__name-sub">Fitness Centre</span></h1>
    <p class="sign__phone">Ph: 9471 2836</p>
  </section>
  <p class="option-label" style="left:250px; top:303px;">1A</p>

  <section class="sign" style="left:621px; top:91px; width:561px; height:188px;">
    <span class="sign__mark sign__mark--round"></span>
    <h2 class="sign__name"><span class="sign__name-main">Ridgeline</span><span class="sign__name-sub">Fitness Centre</span></h2>
    <p class="sign__phone">Ph: 9471 2836</p>
  </section>
  <p class="option-label" style="left:868px; top:303px;">1B</p>

  <section class="sign sign--light" style="left:20px; top:330px;">
    <span class="sign__mark"></span>
    <h2 class="sign__name"><span class="sign__name-main">Ridgeline</span><span class="sign__name-sub">Fitness Centre</span></h2>
    <p class="sign__phone">Ph: 9471 2836</p>
  </section>
  <p class="option-label" style="left:250px; top:535px;">2A</p>

  <section class="sign sign--light" style="left:621px; top:330px; width:561px;">
    <span class="sign__mark sign__mark--round"></span>
    <h2 class="sign__name"><span class="sign__name-main">Ridgeline</span><span class="sign__name-sub">Fitness Centre</span></h2>
    <p class="sign__phone">Ph: 9471 2836</p>
  </section>
  <p class="option-label" style="left:868px; top:535px;">2B</p>

  <section class="sign" style="left:20px; top:568px;">
    <span class="sign__mark"></span>
    <h2 class="sign__name"><span class="sign__name-main">Ridgeline</span><span class="sign__name-sub">Fitness Centre</span></h2>
    <p class="sign__phone">Ph: 9471 2836</p>
  </section>
  <p class="option-label" style="left:250px; top:777px;">3A</p>

  <section class="sign" style="left:621px; top:568px; width:561px; height:188px;">
    <span class="sign__mark sign__mark--round"></span>
    <h2 class="sign__name"><span class="sign__name-main">Ridgeline</span><span class="sign__name-sub">Fitness Centre</span></h2>
    <p class="sign__phone">Ph: 9471 2836</p>
  </section>
  <p class="option-label" style="left:868px; top:777px;">3B</p>

</main>
</body>
</html>
```